Business Card Design needed - Something Awesome!

Need a business card designed. Company is "Marlowe Advisory" we do consulting and also have sales automation technology.
I'm going to use thick stock or metal, something really nice... I was thinking about a QR Code on the back that would just upload my contact info to the persons contact, etc -

This is a Strategy Company with a tech feel. I'm open to ideas but really want this to be nice!

I need a template that should include:

Name | Position or Title
D: 415.902.3376
www.marloweadvisory.example

I'm going to attach my contact so you can use that one, I need to get this printed.

Target Market(s)

Small to mid size customers, Entrepreneurs etc.

Industry/Entity Type

Consulting, Tech, Private Equity.

Contact Information for Business Card

Name, Phone, Maybe email, URL

Font styles to use
Sans Serif

Colors

Designer to choose only greyscale colors for use in the design.

Requirements
Must have
• Fresh, Clean, stand out from the crowd - will be on thick stock or metal.
Nice to have
• Clean, simple yet impactful.
Should not have
• Not cartoonish

```html
<!DOCTYPE html>
<html lang="en">
<head>
<meta charset="utf-8">
<title>Marlowe Advisory — Business Card</title>
<link rel="stylesheet" href="https://fonts.googleapis.com/css2?family=Roboto:wght@300;400;700&display=swap">
<style>
  :root {
    --backdrop: #3a3a3a;
    --card: #0d0d0d;
    --card-edge: #1c1c1c;
    --silver: #d4d4d4;
    --silver-dim: #a9a9a9;
    --rule: #8a8a8a;
    --mark-dark: #1a1a1a;
    --mark-light: #9a9a9a;
  }
  * { margin: 0; padding: 0; box-sizing: border-box; }
  html, body { width: 1200px; height: 801px; overflow: hidden; }
  body {
    background: var(--backdrop);
    font-family: "Roboto", Arial, sans-serif;
    display: flex;
    align-items: center;
    justify-content: center;
    gap: 60px;
  }
  .card {
    position: relative;
    width: 520px;
    height: 297px;
    background: var(--card);
    border: 1px solid var(--card-edge);
    box-shadow: 0 18px 40px rgba(0,0,0,0.45);
  }

  /* Front */
  .identity {
    position: absolute;
    top: 30px;
    right: 30px;
    text-align: right;
  }
  .identity-name {
    color: var(--silver);
    font-weight: 700;
    font-size: 17px;
    letter-spacing: 0.06em;
    text-transform: uppercase;
  }
  .identity-title {
    color: var(--silver-dim);
    font-weight: 400;
    font-size: 13px;
    margin-top: 4px;
  }
  .identity-rule {
    position: absolute;
    top: 86px;
    right: 30px;
    width: 270px;
    height: 1px;
    background: var(--rule);
  }
  .wordmark {
    position: absolute;
    left: 30px;
    top: 112px;
    color: var(--silver);
    font-weight: 300;
    font-size: 34px;
    letter-spacing: 0.04em;
    text-transform: uppercase;
    line-height: 1;
  }
  .contact-rule {
    position: absolute;
    left: 30px;
    top: 196px;
    width: 300px;
    height: 1px;
    background: var(--rule);
  }
  .contact-list {
    position: absolute;
    left: 30px;
    top: 208px;
    list-style: none;
  }
  .contact-list li {
    display: flex;
    align-items: center;
    gap: 8px;
    color: var(--silver);
    font-size: 13px;
    font-weight: 400;
    line-height: 20px;
  }
  .contact-list svg { width: 11px; height: 11px; fill: var(--silver); flex: none; }

  /* Back */
  .card-back {
    display: flex;
    flex-direction: column;
    align-items: center;
    justify-content: center;
    gap: 14px;
  }
  .back-square {
    width: 54px;
    height: 54px;
    background: linear-gradient(135deg, var(--mark-dark), var(--mark-light));
  }
  .back-name {
    color: var(--silver-dim);
    font-weight: 300;
    font-size: 14px;
    letter-spacing: 0.2em;
    text-transform: uppercase;
  }
</style>
</head>
<body>
  <section class="card card-front">
    <div class="identity">
      <p class="identity-name">Adrian K. Holloway</p>
      <p class="identity-title">Founder / CEO</p>
    </div>
    <div class="identity-rule"></div>

    <p class="wordmark">Marlowe Advisory</p>

    <div class="contact-rule"></div>
    <ul class="contact-list">
      <li>
        <svg viewBox="0 0 24 24" aria-hidden="true"><path d="M6.6 10.8a15.1 15.1 0 0 0 6.6 6.6l2.2-2.2a1 1 0 0 1 1-.25 11.4 11.4 0 0 0 3.6.57 1 1 0 0 1 1 1V20a1 1 0 0 1-1 1A17 17 0 0 1 3 4a1 1 0 0 1 1-1h3.5a1 1 0 0 1 1 1c0 1.25.2 2.45.57 3.57a1 1 0 0 1-.25 1z"/></svg>
        415.902.3376
      </li>
      <li>
        <svg viewBox="0 0 24 24" aria-hidden="true"><path d="M2 5h20v14H2zm2 2v.5l8 5 8-5V7l-8 5z"/></svg>
        info@marloweadvisory.example
      </li>
      <li>
        <svg viewBox="0 0 24 24" aria-hidden="true"><path d="M12 2a10 10 0 1 0 0 20 10 10 0 0 0 0-20zm0 2c.9 0 2.2 1.9 2.8 5H9.2C9.8 5.9 11.1 4 12 4zM4.3 11h4.7a20 20 0 0 0 0 2H4.3a8 8 0 0 1 0-2zm10.7 0h4.7a8 8 0 0 1 0 2H15a20 20 0 0 0 0-2zm-5.8 4h5.6c-.6 3.1-1.9 5-2.8 5s-2.2-1.9-2.8-5z"/></svg>
        www.marloweadvisory.example
      </li>
    </ul>
  </section>

  <section class="card card-back">
    <div class="back-square" aria-hidden="true"></div>
    <p class="back-name">Marlowe Advisory</p>
  </section>
</body>
</html>
```